Marlowe Group needs a business card

I would like the card to be simple but modern and elegant.
I like black and white.
or black and gold.
we are a private finance lender and also are involved in property and property developments.

please look at the business card photos i provided i would like M.G only one one side and all the other details on the other side use fonts that tie in with my theme.

Industry/Entity Type

Finance

Contact Information for Business Card

Marlowe Group (M.G) Daniel Marlowe M: 0413586207 E: danmarl@inboxmail.test

Font styles to use
Other font styles liked:
• Use fonts that would reflect our business

Colors
000000
ffffff

Requirements
Must have
• one side of details
• other side has either M.G or Marlowe Group like in the photos provided

```html
<!DOCTYPE html>
<html lang="en">
<head>
<meta charset="utf-8">
<title>Marlowe Group — Business Card</title>
<link rel="stylesheet" href="https://fonts.googleapis.com/css2?family=Cinzel:wght@400;500&family=Source+Sans+3:wght@400;600&display=swap">
<style>
  :root {
    --stage: #000000;
    --card: #2f3033;
    --card-edge: #35363a;
    --gold: #e9c64a;
    --ink-light: #f2f2f2;
    --divider: rgba(255, 255, 255, 0.08);
  }
  * { margin: 0; padding: 0; box-sizing: border-box; }
  html, body {
    width: 1200px;
    height: 900px;
    overflow: hidden;
    background: var(--stage);
  }
  .stage {
    position: relative;
    width: 1200px;
    height: 900px;
    background: var(--stage);
  }
  .card {
    position: absolute;
    top: 271px;
    width: 457px;
    height: 281px;
    border-radius: 14px;
    background: radial-gradient(ellipse at 50% 45%, var(--card-edge), var(--card) 70%);
  }
  .card--details { left: 137px; }
  .card--brand { left: 626px; }

  /* Details side */
  .monogram {
    position: absolute;
    left: 64px;
    top: 91px;
    width: 128px;
    height: 104px;
    display: flex;
    align-items: center;
    justify-content: center;
    font-family: "Cinzel", serif;
    font-weight: 400;
    font-size: 44px;
    letter-spacing: 2px;
    color: var(--gold);
  }
  .divider {
    position: absolute;
    left: 218px;
    top: 84px;
    width: 1px;
    height: 118px;
    background: var(--divider);
  }
  .contact {
    position: absolute;
    left: 237px;
    top: 101px;
    font-family: "Source Sans 3", sans-serif;
  }
  .contact__name {
    font-weight: 600;
    font-size: 17px;
    color: var(--gold);
    margin-bottom: 22px;
  }
  .contact__line {
    display: flex;
    align-items: center;
    gap: 6px;
    font-size: 13px;
    color: var(--ink-light);
    line-height: 20px;
  }
  .contact__icon {
    width: 10px;
    height: 10px;
    fill: var(--gold);
    flex: none;
  }

  /* Brand side */
  .brand {
    position: absolute;
    left: 0;
    right: 0;
    top: 66px;
    display: flex;
    flex-direction: column;
    align-items: center;
    font-family: "Cinzel", serif;
    color: var(--gold);
  }
  .brand__mark {
    font-size: 64px;
    font-weight: 400;
    letter-spacing: 3px;
    line-height: 118px;
  }
  .brand__name {
    margin-top: 12px;
    font-size: 20px;
    font-weight: 400;
    letter-spacing: 1px;
  }
</style>
</head>
<body>
<main class="stage">
  <section class="card card--details" aria-label="Card front with contact details">
    <div class="monogram">M.G</div>
    <div class="divider"></div>
    <div class="contact">
      <p class="contact__name">Daniel Marlowe</p>
      <p class="contact__line">
        <svg class="contact__icon" viewBox="0 0 24 24" aria-hidden="true"><path d="M6.6 10.8a15.1 15.1 0 0 0 6.6 6.6l2.2-2.2a1 1 0 0 1 1-.25 11.4 11.4 0 0 0 3.6.57 1 1 0 0 1 1 1V20a1 1 0 0 1-1 1A17 17 0 0 1 3 4a1 1 0 0 1 1-1h3.5a1 1 0 0 1 1 1c0 1.25.2 2.45.57 3.57a1 1 0 0 1-.25 1z"/></svg>
        0413586207
      </p>
      <p class="contact__line">
        <svg class="contact__icon" viewBox="0 0 24 24" aria-hidden="true"><path d="M2 5h20v14H2z M2 5l10 7 10-7" fill="var(--gold)"/><path d="M2.5 5.5l9.5 6.7 9.5-6.7" fill="none" stroke="var(--card)" stroke-width="1.6"/></svg>
        danmarl@inboxmail.test
      </p>
    </div>
  </section>

  <section class="card card--brand" aria-label="Card back with brand name">
    <div class="brand">
      <div class="brand__mark">M.G</div>
      <div class="brand__name">Marlowe Group</div>
    </div>
  </section>
</main>
</body>
</html>
```